Simple and Clean business card design

We would like the design to be simple clean and to incorporate our colors.

We are open to your design and talent, we have the dots in our logo as we think of it as data points and we connect data points for people.

We are open to see the great creative and clean design you bring to the table

Contact Information for Business Card

please include: name, position, email, phone and website

Font styles to use
Sans Serif

Requirements
Must have
• my colors incorporated, simplicity
Nice to have
• lots of white space, simplicity
Should not have
• complexicity/ complex art

```html
<!DOCTYPE html>
<html lang="en">
<head>
<meta charset="utf-8">
<title>Nodera business card</title>
<link rel="stylesheet" href="https://fonts.googleapis.com/css2?family=Montserrat:wght@600&family=Open+Sans:wght@400;700&display=swap">
<style>
  :root {
    --stage: #2b2b2b;
    --paper: #ffffff;
    --yellow: #f6c212;
    --green: #35a955;
    --blue: #4a8cf0;
    --red: #e8483a;
    --ink: #111111;
    --name-blue: #4a8cf0;
  }
  html, body {
    margin: 0;
    width: 1200px;
    height: 901px;
    overflow: hidden;
    background: var(--stage);
    font-family: "Open Sans", sans-serif;
  }
  .sheet {
    width: 1200px;
    height: 901px;
    display: flex;
    flex-direction: column;
    align-items: center;
    justify-content: center;
    gap: 36px;
  }
  .card {
    position: relative;
    width: 700px;
    height: 400px;
    background: var(--paper);
    overflow: hidden;
    box-shadow: 0 6px 18px rgba(0,0,0,.45);
  }
  .card-band {
    position: absolute;
    left: 0;
    top: 0;
    width: 700px;
    height: 110px;
    background: linear-gradient(90deg, var(--blue) 0%, var(--green) 30%, var(--yellow) 60%, var(--red) 100%);
    opacity: .9;
  }
  .brand {
    position: absolute;
    display: flex;
    align-items: center;
    gap: 14px;
    font-family: "Montserrat", sans-serif;
    font-weight: 600;
    color: var(--ink);
    letter-spacing: 1px;
    line-height: 1;
  }
  .brand-dot {
    border-radius: 50%;
    background: var(--blue);
  }
  .card-front .brand {
    left: 50%;
    top: 200px;
    transform: translateX(-50%);
    font-size: 64px;
  }
  .card-front .brand-dot { width: 22px; height: 22px; }
  .card-back .brand { right: 50px; top: 180px; font-size: 58px; }
  .card-back .brand-dot { width: 20px; height: 20px; }
  .holder {
    position: absolute;
    left: 50px;
    top: 228px;
  }
  .holder-name {
    margin: 0;
    font-weight: 700;
    font-size: 27px;
    color: var(--name-blue);
    line-height: 1.1;
  }
  .holder-role {
    margin: 0;
    font-size: 17px;
    color: var(--ink);
  }
  .divider {
    position: absolute;
    left: 40px;
    right: 40px;
    top: 292px;
    height: 1.5px;
    background: var(--ink);
  }
  .contacts {
    position: absolute;
    left: 40px;
    top: 302px;
    margin: 0;
    padding: 0;
    list-style: none;
    font-size: 19px;
    color: var(--ink);
    line-height: 28px;
  }
  .contacts li { display: flex; align-items: center; gap: 10px; }
  .contact-icon { width: 20px; height: 20px; flex: none; }
  .address {
    position: absolute;
    right: 40px;
    top: 320px;
    margin: 0;
    text-align: right;
    font-size: 19px;
    line-height: 26px;
    color: var(--ink);
  }
</style>
</head>
<body>
<main class="sheet">

  <section class="card card-front">
    <div class="card-band" role="img" aria-label="Decorative colour band in blue, green, yellow and red"></div>
    <div class="brand"><span class="brand-dot"></span>Nodera</div>
  </section>

  <section class="card card-back">
    <div class="card-band" role="img" aria-label="Decorative colour band in blue, green, yellow and red"></div>

    <div class="holder">
      <p class="holder-name">Daniel Reyes</p>
      <p class="holder-role">Manager</p>
    </div>

    <div class="brand"><span class="brand-dot"></span>Nodera</div>

    <div class="divider"></div>

    <ul class="contacts">
      <li>
        <svg class="contact-icon" viewBox="0 0 20 20" aria-hidden="true"><rect width="20" height="20" rx="4" fill="var(--blue)"/><path d="M6,4 L8.5,4 L9.5,7 L8,8.2 Q9.5,11 11.8,12 L13,10.5 L16,11.5 L16,14 Q15,16 12.5,15.5 Q6,13.5 4.5,7.5 Q4,5 6,4 Z" fill="#fff"/></svg>
        555-014-2100
      </li>
      <li>
        <svg class="contact-icon" viewBox="0 0 20 20" aria-hidden="true"><rect width="20" height="20" rx="4" fill="var(--blue)"/><rect x="4" y="6" width="12" height="8.5" fill="none" stroke="#fff" stroke-width="1.5"/><path d="M4,6 L10,11 L16,6" fill="none" stroke="#fff" stroke-width="1.5"/></svg>
        hello@noderamail.com
      </li>
      <li>
        <svg class="contact-icon" viewBox="0 0 20 20" aria-hidden="true"><rect width="20" height="20" rx="4" fill="var(--blue)"/><circle cx="10" cy="10" r="5.5" fill="none" stroke="#fff" stroke-width="1.5"/><path d="M4.5,10 H15.5 M10,4.5 Q7,10 10,15.5 M10,4.5 Q13,10 10,15.5" fill="none" stroke="#fff" stroke-width="1.2"/></svg>
        www.noderadata.com
      </li>
    </ul>

    <p class="address">Your address, city<br>state, ZIP 0000</p>
  </section>

</main>
</body>
</html>
```